Nutritional & Gastrointestinal Health Consulting Service-Website design

We need a website design for a new health consulting service called "Bright Vale" based in Perth, Australia.

We will be providing consulting services in the areas of:
1) Nutrition and Diet
2) Gastrointestinal Health (which means stomach & digestive system related health)

These consulting services will be provided by an Accredited Dietitian and a Paediatric Gastroenterologist.

We are open to creative ideas in terms of design, layout, fonts and colours. We also would love to see images of nature in the backdrop with families (adults with kids) having a good time, fresh fruits and vegetables displayed in a farmer's market or supermarket. 2 or 3 images should be sufficient. We would also definitely want our logo somewhere in the main page of website. The logo file is also attached. Please have a look at a website's design that we really liked. We would love to see designs inspired by that style. The website details are in the in the "nice to have priorities" section of this project brief.

We also would be looking at website designers with software coding skills so that if we like the design we can go ahead with the next step of coding.

The website design should communicate the purpose of the website and at the same time be simple, elegant and unique/eye-catching.

We look forward to receiving creative ideas for our website from you all. Good luck!

More details have been added to our project- for example: Logo, fonts style, must haves etc etc. Please view the updated project brief. Looking forward to receiving your fantastic ideas for our website. Thanking you

Hi, I have updated the colour preference. Will add the content preferences tomorrow. thanks

Hello all, I have now added a LOT more content to what we want in our website. It is very much in detail, so please carefully have a read through the entire project brief. If you have any questions write back to me and I will try to respond as quickly as I can. Last few days were busy so couldn't respond quickly to all of you who had send me designs/queries/questions. Thank you for your patience. I look forward to receiving fantastic designs from you all. Good Luck :-)

Target Market(s)

Adults based in western speaking countries aged 18 to 60 years

Industry/Entity Type

Software

Font styles to use
Sans Serif
Script

Colors
faa54b
acd036

Requirements
Must have
• The website must have the MAIN logo file attached. I have attached 3 files: 1) MAIN logo; 2) supplementary logo A ; 3) supplementary logo B

I have selected 2 colours from the colour scheme (see below)-(as the colour of our logo is that).
However we would also like to see LIGHT CHOCOLATE BROWN or CHOCOLATE BROWN colour used as the background colour of the website
Preferred WEBSITE CONTENT:
1) HOME PAGE:
Content required=
--Company Logo
--Dr Dorian Pelham
Paediatric Gastroenterologist & Hepatologist
-Marla Pelham.
Dietitian & Nutritionist
--Website Menu (either listed horizontally or vertically):
Once clicked on each name:

Under each of the Website Menu items we want the following Headings to be added

2) ABOUT US page:
Sub-heading under this: Qualification, Skills, Special Interest

3) SERVICES
DORIAN'S PAGE: Individual Consultation, Endoscopy procedures
Individual Consultation, Group Based Services, Food Diary, Food & Symptom Diary

4) FEES & REBATE: Content as below:
Please Note: Payment of full fees is required at the time of consultation and procedures. 48 hours notice is required for cancellation of appointments/non-attendance. Failure to provide this may result in a fee being incurred. Please call reception to find out the amount of fee charged for cancellation of appointments/non-attendance.
headings are:
Paediatric Gastroenterology:
Dorian's pge
Individual Consultation - Initial (upto 30 mins):
Review Consultation (upto 15 mins):
Endoscopy procedures - No Gap fees charged. Fees will be billed directly to Vitacover. If any queries, please contact reception.

marla's pge
sub heading:
Individual Consultation - Initial (upto 45 mins):
Individual Consultation - Review (upto 30 mins):

Concession-Individual Consultation -Initial (upto 45 mins):
Concession-Individual Consultation - Review (upto 30 mins):
Please Note: Concession applies for health care card holders & pensioners

Group Based Services: Pricing subject to the type of service provided. Please contact us for an obligation free quote.
Education Topics Include:
- Paediatric Nutrition (Introducing Solids, Fussy Eating, Healthy Eating)
- Pregnancy Nutrition, Gestational Diabetes, Breastfeeding/Lactation Nutrition
- Healthy Eating, Supermarket Shopping Tips, Nutrition Label Reading Tips, Healthier
sub heading under nutrition & diet:
-Vitacover:
--A rebate of $52.95 is available from Vitacover if an EPC ( Enhanced Primary Care)/Chronic Disease Management (CDM) plan is issued by your GP.
--All mandatory paperwork needs to be available at the time of making your appointment for your eligibility.
-Private Health Fund:
--Most private health funds provide rebate on dietetic appointments. However the rebate amount depends on your level of cover. Thus, please contact your health fund to determine your entitled rebate.
-RSB: Approved provider for RSB services

6) FOR DOCTORS: Bright Vale Paediatric Gastroenterologist Referral Form
Bright Vale Dietitian Referral form
7) LOCATIONS & CONTACT

Paediatric Gastroenterology & Hepatology Service
Suite 46
Holy Lantern Bramcote Medical Centre
17 Colin Ferris Pde,
MURDOCH, WA 6150
P: (08) 9422 5061
F: (08) 9422 3094

Nutrition & Diet Service
Suite 46
17 Colin Ferris Pde,
MURDOCH, WA 6150
P: (08) 9422 5061
F: (08) 9422 3094

Tolland Medical Centre
58-60 Karrigan Parkway,
MANDURAH, WA 6210
P: (08) 9647 2283
F: (08) 96724419
www.tmcexample.com.au

This page should have a webform that has following titles:
-Your Name
-Your Email
-Your Phone
-Message

8) NEWS & BLOG
Nice to have
• We liked the design style of the websites below:
https://www.vendoraplex.example/

http://qoravelt.example/

But feel free to use your creativity too
Should not have
• Please do not use any body building or muscle building images

```html
<!DOCTYPE html>
<html lang="en">
<head>
<meta charset="utf-8">
<title>Bright Vale</title>
<link rel="stylesheet" href="https://fonts.googleapis.com/css2?family=Open+Sans:wght@400;600;800&display=swap">
<style>
  :root {
    --brown-deep: #46271f;
    --brown-warm: #5e362d;
    --brown-glow: #6b3e33;
    --orange: #faa54b;
    --green: #acd036;
    --green-band: #93c517;
    --button: #b87a3c;
    --button-edge: #6e4322;
    --white: #ffffff;
  }
  * { box-sizing: border-box; margin: 0; padding: 0; }
  html, body { width: 1200px; height: 843px; overflow: hidden; }
  body {
    font-family: "Open Sans", Arial, sans-serif;
    background: radial-gradient(ellipse at 100% 0%, var(--brown-glow) 0%, var(--brown-warm) 35%, var(--brown-deep) 100%);
    position: relative;
  }
  .service-band {
    position: absolute;
    height: 34px;
    color: var(--white);
    font-size: 16px;
    line-height: 34px;
    padding-left: 28px;
    transform: rotate(-5deg);
    transform-origin: left center;
    box-shadow: 2px 4px 6px rgba(0,0,0,.45);
  }
  .service-band--nutrition { left: 226px; top: 192px; width: 290px; background: var(--orange); z-index: 1; }
  .service-band--gastro { left: 690px; top: 180px; width: 478px; background: var(--green-band); z-index: 3; }
  .brand-disc {
    position: absolute;
    left: 466px; top: 188px;
    width: 268px; height: 268px;
    border-radius: 50%;
    background: var(--orange);
    z-index: 2;
  }
  .menu { list-style: none; }
  .menu-item {
    position: absolute;
    height: 34px;
    background: var(--button);
    border: 1px solid var(--button-edge);
    color: var(--white);
    font-size: 15px;
    font-weight: 600;
    letter-spacing: 1.5px;
    line-height: 32px;
    z-index: 1;
  }
  .menu--left .menu-item { padding-left: 20px; }
  .menu--right .menu-item { text-align: right; padding-right: 20px; }
  .brand-name {
    position: absolute;
    left: 0; right: 0; top: 520px;
    text-align: center;
    font-family: "Open Sans", Arial, sans-serif;
    font-weight: 800;
    font-size: 132px;
    letter-spacing: 2px;
    color: var(--green);
  }
</style>
</head>
<body>
  <div class="service-band service-band--nutrition">Nutrition and Diet Services</div>
  <div class="service-band service-band--gastro">Paediatric Gastroenterology &amp; Hepatology Services</div>

  <nav aria-label="Nutrition and diet menu">
    <ul class="menu menu--left">
      <li class="menu-item" style="left:359px;top:242px;width:108px">About</li>
      <li class="menu-item" style="left:293px;top:290px;width:174px">Fees &amp; Rebate</li>
      <li class="menu-item" style="left:316px;top:337px;width:159px">For Doctors</li>
      <li class="menu-item" style="left:326px;top:385px;width:149px">News &amp; Blog</li>
      <li class="menu-item" style="left:245px;top:432px;width:235px">Locations &amp; Contact</li>
    </ul>
  </nav>

  <div class="brand-disc"></div>

  <nav aria-label="Gastroenterology menu">
    <ul class="menu menu--right">
      <li class="menu-item" style="left:727px;top:242px;width:131px">About us</li>
      <li class="menu-item" style="left:736px;top:290px;width:173px">Fees &amp; Rebate</li>
      <li class="menu-item" style="left:727px;top:337px;width:153px">For Doctors</li>
      <li class="menu-item" style="left:727px;top:385px;width:141px">For Patient</li>
      <li class="menu-item" style="left:684px;top:432px;width:237px">Locations &amp; Contact</li>
    </ul>
  </nav>

  <h1 class="brand-name">Bright Vale</h1>
</body>
</html>
```